4D Cradle Glimpse Luxury Ultrasound Billboard

Design a HIGH-END, MODERN billboard for my private prenatal ultrasound studio, 4D Cradle Glimpse, located in Pace, Florida.
This billboard will be viewed by drivers traveling at highway speeds, so it must be extremely clean, simple, and readable within 6 seconds.
About My Business
4D Cradle Glimpse is a private prenatal ultrasound studio specializing in:
Highest technology 4D/HD Ultrasounds
Early Gender Determination
Pregnancy Confirmation
I have been serving families for nearly 10 years and is known for creating a memorable experience, not just an ultrasound appointment.
Design Style
I DO NOT want:
Flowers
Leaves
Swirls
Glitter
Hearts everywhere
Busy backgrounds
Generic maternity stock graphics
I DO want:
Modern
Luxury
Upscale
Clean
Professional
Eye-catching
Premium medical spa feel
Colors
Use colors from my logo:
LOGO Green ( or a deep green)
Black
White
Soft Gold accents
Images:
Incorporate my professional headshot in a clean, modern way, logo, and the ultrasound images
Text
Keep wording minimal.
Primary Headline ( OPEN TO IDEAS) :
EXAMPLES ( WOULD RATHER SOMETHING MORE CATCHY)
" ADVANCED IMAGING. UNFORGETTABLE MOMENTS"
"MEET YOUR BABY BEFORE BIRTH"
Under headline:
4D Ultrasound • Early Gender • Pregnancy Confirmation
Business Name:
4D Cradle Glimpse
Private Prenatal Ultrasound Studio
Phone Number:
850-471-5923
Important
This billboard must be readable in 5–6 seconds from a moving vehicle.
Less text is better.
The phone number and business name must be visible from a distance.
The design should feel like a premium brand that immediately tells expecting parents:
“This is where I go to see my baby.”
Files Provided
Official logo
Headshot
Ultrasound images
Don’t make this look like a medical office billboard.
Make it look like a luxury baby experience billboard. That’s what separates 4D Cradle Glimpse from hospitals, OB offices, and all the new studios popping up around you. The emotional connection is what gets moms to book. ❤️
Billboard Size - 10.6” x 36”

```html
<!DOCTYPE html>
<html lang="en">
<head>
<meta charset="utf-8">
<title>4D Cradle Glimpse – Billboard Options</title>
<link rel="stylesheet" href="https://fonts.googleapis.com/css2?family=Poppins:wght@400;500;600;700;800&family=Playfair+Display:wght@500&display=swap">
<style>
  :root {
    --board-grey: #6e6f73;
    --deep-green: #173330;
    --gold: #c9963f;
    --gold-light: #e6b75a;
    --gold-dark: #a9782b;
    --white: #ffffff;
    --ink: #14302c;
  }
  * { box-sizing: border-box; margin: 0; padding: 0; }
  html, body { width: 1200px; height: 941px; overflow: hidden; }
  body {
    background: var(--board-grey);
    font-family: "Poppins", sans-serif;
    position: relative;
  }
  .option-label {
    position: absolute;
    left: 0; width: 1200px;
    text-align: center;
    color: var(--white);
    font-family: "Poppins", sans-serif;
    font-weight: 400;
    font-size: 28px;
    letter-spacing: 1px;
  }
  .option-label--one { top: 46px; }
  .option-label--two { top: 512px; }

  .billboard {
    position: absolute;
    left: 46px;
    width: 1108px;
    height: 323px;
    background: var(--white);
    overflow: hidden;
    box-shadow: 0 12px 18px rgba(0,0,0,0.35);
  }
  .billboard--one { top: 112px; }
  .billboard--two { top: 569px; }

  .headshot {
    position: absolute;
    left: 0; top: 0;
    width: 270px; height: 323px;
    background: linear-gradient(90deg, #d9d2c8 0%, #c8bfb2 40%, #e9e6e1 75%, rgba(255,255,255,0) 100%);
  }
  .shapes { position: absolute; inset: 0; width: 1108px; height: 323px; }

  .headline {
    position: absolute;
    left: 262px; top: 16px;
    width: 290px;
    text-align: center;
    color: var(--ink);
  }
  .headline__top, .headline__bottom {
    display: block;
    font-family: "Poppins", sans-serif;
    font-weight: 700;
    letter-spacing: -2px;
    line-height: 1;
  }
  .headline__top { font-size: 53px; }
  .headline__accent {
    display: block;
    font-family: "Playfair Display", serif;
    font-weight: 500;
    font-size: 90px;
    line-height: 0.82;
    margin-top: 2px;
    color: var(--gold);
    background: linear-gradient(180deg, var(--gold-light), var(--gold-dark));
    -webkit-background-clip: text;
    background-clip: text;
    -webkit-text-fill-color: transparent;
  }
  .headline__bottom { font-size: 42px; margin-top: 4px; letter-spacing: -1.5px; }

  .rule {
    position: absolute;
    left: 241px; top: 192px;
    width: 328px; height: 2px;
    background: linear-gradient(90deg, rgba(201,150,63,0), var(--gold) 15%, var(--gold) 85%, rgba(201,150,63,0));
  }
  .services {
    position: absolute;
    left: 238px; top: 205px;
    width: 336px;
    text-align: center;
    font-weight: 700;
    font-size: 10px;
    color: var(--ink);
    white-space: nowrap;
  }
  .phone {
    position: absolute;
    left: 240px; top: 226px;
    display: flex; align-items: center; gap: 9px;
  }
  .phone__icon { width: 31px; height: 31px; }
  .phone__number {
    font-weight: 800;
    font-size: 41px;
    color: var(--ink);
    letter-spacing: -0.5px;
    line-height: 1;
  }
  .location {
    position: absolute;
    left: 257px; top: 277px;
    width: 295px; height: 46px;
    display: flex; align-items: center; justify-content: center; gap: 10px;
    padding-top: 2px;
    color: var(--white);
    font-size: 17px;
    letter-spacing: 3.5px;
  }
  .location__pin { width: 14px; height: 18px; }

  .brand-card {
    position: absolute;
    left: 873px; top: 34px;
    width: 204px; height: 128px;
    background: var(--white);
    border-radius: 10px;
    border: 2px solid var(--white);
    outline: 1.5px solid var(--deep-green);
    outline-offset: -6px;
    display: flex; flex-direction: column; align-items: center; justify-content: center;
    text-align: center;
  }
  .brand-card__name {
    font-family: "Poppins", sans-serif;
    font-weight: 700;
    font-size: 22px;
    line-height: 1.1;
    color: var(--gold);
  }
  .brand-card__line {
    width: 150px; height: 1px; background: var(--gold); margin: 8px 0 6px;
  }
  .brand-card__tag {
    font-size: 7.5px;
    font-weight: 500;
    color: #5a6462;
    letter-spacing: 0.4px;
  }

  .owned-band {
    position: absolute;
    left: 844px; top: 179px;
    width: 264px; height: 43px;
    background: linear-gradient(180deg, var(--gold-light), var(--gold-dark));
    display: flex; align-items: center; justify-content: center;
    font-weight: 800;
    font-size: 23px;
    color: var(--ink);
    letter-spacing: -0.3px;
  }
  .tagline {
    position: absolute;
    left: 850px; top: 232px;
    width: 258px;
    text-align: center;
    color: var(--white);
    font-size: 17px;
    line-height: 23px;
  }
  .tagline--stats { top: 232px; font-size: 20px; line-height: 28px; }
  .tagline strong { font-weight: 700; }
  .tagline-rule {
    position: absolute;
    left: 906px; top: 291px;
    width: 142px; height: 1px;
    background: linear-gradient(90deg, rgba(201,150,63,0), var(--gold), rgba(201,150,63,0));
  }
</style>
</head>
<body>

<p class="option-label option-label--one">OPTION -01</p>

<section class="billboard billboard--one">
  <div class="headshot" role="img" aria-label="Portrait of the studio owner seated, holding an ultrasound probe"></div>
  <svg class="shapes" viewBox="0 0 1108 323" preserveAspectRatio="none">
    <defs>
      <linearGradient id="goldStroke1" x1="0" y1="0" x2="0" y2="1">
        <stop offset="0" stop-color="#e6b75a"/><stop offset="1" stop-color="#a9782b"/>
      </linearGradient>
      <radialGradient id="scanTone1" cx="0.45" cy="0.45" r="0.7">
        <stop offset="0" stop-color="#b8736a"/><stop offset="0.6" stop-color="#8a4a40"/><stop offset="1" stop-color="#2a1614"/>
      </radialGradient>
    </defs>
    <path d="M790 0 H1108 V323 H790 Z" fill="#173330"/>
    <path role="img" aria-label="4D ultrasound image of twin babies face to face"
          d="M628 0 C575 70 575 180 612 323 H800 C855 240 860 120 797 0 Z" fill="url(#scanTone1)"/>
    <path d="M628 0 C575 70 575 180 612 323" fill="none" stroke="url(#goldStroke1)" stroke-width="5"/>
    <path d="M797 0 C860 120 855 240 800 323" fill="none" stroke="url(#goldStroke1)" stroke-width="5"/>
    <path d="M257 323 L303 280 H506 L552 323 Z" fill="#173330" stroke="#c9963f" stroke-width="2.5"/>
  </svg>

  <h1 class="headline">
    <span class="headline__top">MEET YOUR</span>
    <span class="headline__accent">BABY</span>
    <span class="headline__bottom">BEFORE BIRTH</span>
  </h1>
  <div class="rule"></div>
  <p class="services">4D ULTRASOUND • EARLY GENDER • PREGNANCY CONFIRMATION</p>
  <div class="phone">
    <svg class="phone__icon" viewBox="0 0 32 32">
      <circle cx="16" cy="16" r="16" fill="#c9963f"/>
      <path d="M11 8.5c1-.6 2-.3 2.5.6l1.5 3c.4.8.1 1.6-.6 2.1l-1.2.8c.8 2 2.4 3.7 4.4 4.6l.9-1.2c.5-.7 1.4-.9 2.1-.5l3 1.6c.9.5 1.1 1.5.5 2.4l-1 1.4c-.7 1-2 1.4-3.2 1-5.2-1.7-9.2-5.8-10.8-11-.4-1.2.1-2.5 1.1-3.1z" fill="#fff"/>
    </svg>
    <span class="phone__number">850-471-5923</span>
  </div>
  <p class="location">
    <svg class="location__pin" viewBox="0 0 14 18"><path d="M7 0C3.1 0 0 3 0 6.9 0 12 7 18 7 18s7-6 7-11.1C14 3 10.9 0 7 0zm0 9.5a2.6 2.6 0 1 1 0-5.2 2.6 2.6 0 0 1 0 5.2z" fill="#c9963f"/></svg>
    PACE, FLORIDA
  </p>

  <div class="brand-card">
    <span class="brand-card__name">4D Cradle<br>Glimpse</span>
    <span class="brand-card__line"></span>
    <span class="brand-card__tag">PRENATAL ULTRASOUND STUDIO</span>
  </div>
  <div class="owned-band">LOCALLY OWNED</div>
  <p class="tagline">More than just an<br>Ultrasound Experience</p>
  <div class="tagline-rule"></div>
</section>

<p class="option-label option-label--two">OPTION -02</p>

<section class="billboard billboard--two">
  <div class="headshot" role="img" aria-label="Portrait of the studio owner seated, holding an ultrasound probe"></div>
  <svg class="shapes" viewBox="0 0 1108 323" preserveAspectRatio="none">
    <defs>
      <linearGradient id="goldStroke2" x1="0" y1="0" x2="0" y2="1">
        <stop offset="0" stop-color="#e6b75a"/><stop offset="1" stop-color="#a9782b"/>
      </linearGradient>
      <radialGradient id="scanTone2" cx="0.45" cy="0.45" r="0.7">
        <stop offset="0" stop-color="#b8736a"/><stop offset="0.6" stop-color="#8a4a40"/><stop offset="1" stop-color="#2a1614"/>
      </radialGradient>
    </defs>
    <path d="M790 0 H1108 V323 H790 Z" fill="#173330"/>
    <path role="img" aria-label="4D ultrasound image of twin babies face to face"
          d="M628 0 C575 70 575 180 612 323 H800 C855 240 860 120 797 0 Z" fill="url(#scanTone2)"/>
    <path d="M628 0 C575 70 575 180 612 323" fill="none" stroke="url(#goldStroke2)" stroke-width="5"/>
    <path d="M797 0 C860 120 855 240 800 323" fill="none" stroke="url(#goldStroke2)" stroke-width="5"/>
    <path d="M257 323 L303 280 H506 L552 323 Z" fill="#173330" stroke="#c9963f" stroke-width="2.5"/>
  </svg>

  <h1 class="headline">
    <span class="headline__top">MEET YOUR</span>
    <span class="headline__accent">BABY</span>
    <span class="headline__bottom">BEFORE BIRTH</span>
  </h1>
  <div class="rule"></div>
  <p class="services">4D ULTRASOUND • EARLY GENDER • PREGNANCY CONFIRMATION</p>
  <div class="phone">
    <svg class="phone__icon" viewBox="0 0 32 32">
      <circle cx="16" cy="16" r="16" fill="#c9963f"/>
      <path d="M11 8.5c1-.6 2-.3 2.5.6l1.5 3c.4.8.1 1.6-.6 2.1l-1.2.8c.8 2 2.4 3.7 4.4 4.6l.9-1.2c.5-.7 1.4-.9 2.1-.5l3 1.6c.9.5 1.1 1.5.5 2.4l-1 1.4c-.7 1-2 1.4-3.2 1-5.2-1.7-9.2-5.8-10.8-11-.4-1.2.1-2.5 1.1-3.1z" fill="#fff"/>
    </svg>
    <span class="phone__number">850-471-5923</span>
  </div>
  <p class="location">
    <svg class="location__pin" viewBox="0 0 14 18"><path d="M7 0C3.1 0 0 3 0 6.9 0 12 7 18 7 18s7-6 7-11.1C14 3 10.9 0 7 0zm0 9.5a2.6 2.6 0 1 1 0-5.2 2.6 2.6 0 0 1 0 5.2z" fill="#c9963f"/></svg>
    PACE, FLORIDA
  </p>

  <div class="brand-card">
    <span class="brand-card__name">4D Cradle<br>Glimpse</span>
    <span class="brand-card__line"></span>
    <span class="brand-card__tag">PRENATAL ULTRASOUND STUDIO</span>
  </div>
  <div class="owned-band">LOCALLY OWNED</div>
  <p class="tagline tagline--stats"><strong>10 years.</strong><br>Thousands of Babies</p>
  <div class="tagline-rule"></div>
</section>

</body>
</html>
```